Business Card Design

We provide services doing multiple jobs in the construction industry.Please note: The company name needs to be ROCK SOLID BUILDING SERVICESAttached logo was an example of what we wanted. Can you change up the colors?

Industry/Entity Type

Construction

Contact Information for Business Card

ROCK SOLID BUILDING SERVICES5401 HUDSON BEND RDAUSTIN, TX 78734(512)243-6854ROCKSOLIDBUILDINGSERVICES@GMAIL.COM

```html
<!DOCTYPE html>
<html lang="en">
<head>
<meta charset="utf-8">
<title>Pearlwood Framing Works – Business Card</title>
<link rel="stylesheet" href="https://fonts.googleapis.com/css2?family=Questrial&display=swap">
<style>
  :root {
    --backdrop: #e9e8ee;
    --card-light: #ffffff;
    --card-grey: #e3e3e6;
    --navy: #25246e;
    --navy-deep: #1a1955;
    --navy-bright: #3b3a92;
    --swoosh-dark: #1b1b1f;
    --swoosh-mid: #8a8a90;
    --ink-light: #ffffff;
  }
  * { margin: 0; padding: 0; box-sizing: border-box; }
  html, body { width: 1200px; height: 900px; overflow: hidden; }
  body {
    background: var(--backdrop);
    font-family: "Questrial", "Century Gothic", sans-serif;
    position: relative;
  }
  .card {
    position: absolute;
    left: 100px;
    top: 164px;
    width: 1000px;
    height: 572px;
    border-radius: 44px;
    overflow: hidden;
    box-shadow: 0 18px 40px rgba(20, 20, 60, 0.18);
  }
  .card-art { position: absolute; inset: 0; width: 100%; height: 100%; }
  .brand {
    position: absolute;
    left: 64px;
    top: 74px;
    color: var(--navy);
    display: flex;
    flex-direction: column;
    letter-spacing: 2px;
  }
  .brand-name { font-size: 52px; line-height: 1; }
  .brand-sub { font-size: 25px; line-height: 1.3; letter-spacing: 5px; }
  .contact {
    position: absolute;
    right: 60px;
    top: 192px;
    text-align: right;
    color: var(--ink-light);
  }
  .contact-name { font-size: 24px; letter-spacing: 2px; line-height: 1.2; }
  .contact-title { font-size: 14px; letter-spacing: 2px; margin-top: 2px; margin-bottom: 22px; }
  .contact-line {
    display: flex;
    justify-content: flex-end;
    align-items: center;
    gap: 10px;
    font-size: 17px;
    letter-spacing: 1px;
    height: 30px;
  }
  .contact-line svg { width: 16px; height: 16px; fill: none; stroke: var(--ink-light); stroke-width: 1.6; }
  .address {
    position: absolute;
    right: 60px;
    bottom: 62px;
    color: var(--ink-light);
    font-size: 24px;
    letter-spacing: 1.5px;
  }
</style>
</head>
<body>
  <div class="card">
    <svg class="card-art" viewBox="0 0 1000 572" preserveAspectRatio="none" aria-hidden="true">
      <defs>
        <linearGradient id="paper" x1="0" y1="0" x2="0.6" y2="1">
          <stop offset="0" stop-color="var(--card-grey)"/>
          <stop offset="0.45" stop-color="var(--card-light)"/>
          <stop offset="1" stop-color="var(--card-grey)"/>
        </linearGradient>
        <linearGradient id="navyFill" x1="0" y1="0" x2="1" y2="1">
          <stop offset="0" stop-color="var(--navy-deep)"/>
          <stop offset="0.55" stop-color="var(--navy-bright)"/>
          <stop offset="1" stop-color="var(--navy)"/>
        </linearGradient>
        <linearGradient id="swoosh" x1="0" y1="0" x2="1" y2="0">
          <stop offset="0" stop-color="var(--swoosh-mid)"/>
          <stop offset="0.3" stop-color="var(--swoosh-dark)"/>
          <stop offset="0.75" stop-color="var(--swoosh-dark)"/>
          <stop offset="1" stop-color="var(--swoosh-mid)"/>
        </linearGradient>
      </defs>
      <rect width="1000" height="572" fill="url(#paper)"/>
      <path d="M0,292 C150,345 260,366 420,300 C600,226 760,110 1000,66 L1000,82 C760,128 600,250 420,320 C260,382 150,362 0,314 Z" fill="url(#swoosh)"/>
      <path d="M0,332 C150,372 260,392 420,334 C600,264 760,146 1000,100 L1000,572 L0,572 Z" fill="url(#navyFill)"/>
    </svg>

    <div class="brand">
      <span class="brand-name">PEARLWOOD</span>
      <span class="brand-sub">FRAMING WORKS</span>
    </div>

    <div class="contact">
      <div class="contact-name">DANA WHITCOMBE</div>
      <div class="contact-title">PRESIDENT</div>
      <div class="contact-line">(512)555-0193
        <svg viewBox="0 0 16 16"><path d="M4 2 L6 5 L5 7 C6 9 7 10 9 11 L11 10 L14 12 L12 14 C7 14 2 9 2 4 Z"/></svg>
      </div>
      <div class="contact-line">(512)555-0194
        <svg viewBox="0 0 16 16"><rect x="4.5" y="1.5" width="7" height="13" rx="1"/><line x1="7" y1="12" x2="9" y2="12"/></svg>
      </div>
      <div class="contact-line">(512)555-0195
        <svg viewBox="0 0 16 16"><rect x="2" y="6" width="12" height="7"/><rect x="4.5" y="2" width="7" height="4"/><line x1="5" y1="9.5" x2="11" y2="9.5"/></svg>
      </div>
      <div class="contact-line">pearlwoodframingworks@mailnest.example
        <svg viewBox="0 0 16 16"><rect x="1.5" y="3.5" width="13" height="9"/><path d="M1.5 3.5 L8 9 L14.5 3.5"/></svg>
      </div>
      <div class="contact-line">www.pearlwoodframing.example
        <svg viewBox="0 0 16 16"><circle cx="8" cy="8" r="6.5"/><ellipse cx="8" cy="8" rx="3" ry="6.5"/><line x1="1.5" y1="8" x2="14.5" y2="8"/></svg>
      </div>
    </div>

    <div class="address">7732 FERNGLEN PASS LN, AUSTIN, TX 78734</div>
  </div>
</body>
</html>
```